Business Card Design Project

Looking for a logo and business card for a Real State Business i will be opening. The name is not choosen yet , but will probably be RWT IMOVEIS.
I was thinking black and silver colors, but am open to nice ideas.
I did add a business card that i liked a lot, am looking for something like that, with logo in black or silver in a black card. The logo i was thinking in the letters RWT as i uploaded or something or little and cute buildings or a house...just ideas, can be any nice logo.
Updates

You guys can add other colors if you want, I like colors very "BRIGHT" and "open", like red, pink, strong colors. almost glow in the dark colors. lol

Designers,

I've increased more 88 dollars in the budget for 1st place cause I will want envelope designs... small and big sizes.

So 1st place is now U$248,00. 

No need to send the envelope designs right now... only the business cards designs.

Thank you.

Industry/Entity Type

Business

Requirements
Must have
• Marcela Tavares Rocha

www.RWTimoveis-exemplo.com.br

+554187316042

marcela@rwtimoveis-exemplo.com.br

```html
<!DOCTYPE html>
<html lang="pt-BR">
<head>
<meta charset="utf-8">
<title>RWT Imóveis — Cartão de visita</title>
<link rel="stylesheet" href="https://fonts.googleapis.com/css2?family=Cabin:wght@400;700&display=swap">
<style>
  :root {
    --page-bg: #eceeed;
    --card-bg: #1e1e1d;
    --ink-light: #f2f2f2;
    --ink-silver: #b9b9b9;
    --shadow: rgba(0, 0, 0, 0.35);
  }
  * { margin: 0; padding: 0; box-sizing: border-box; }
  html, body {
    width: 1200px;
    height: 642px;
    overflow: hidden;
    background: var(--page-bg);
    font-family: "Cabin", sans-serif;
  }
  .canvas {
    position: relative;
    width: 1200px;
    height: 642px;
  }
  .card {
    position: absolute;
    background: var(--card-bg);
    box-shadow: 1px 3px 5px var(--shadow);
  }
  .card--front {
    left: 120px;
    top: 148px;
    width: 477px;
    height: 276px;
  }
  .card--back {
    left: 630px;
    top: 151px;
    width: 470px;
    height: 271px;
  }
  .brand {
    position: absolute;
    left: 0;
    right: 0;
    top: 62px;
    display: flex;
    flex-direction: column;
    align-items: center;
    gap: 22px;
  }
  .brand__mark {
    width: 30px;
    height: 30px;
    border: 2px solid var(--ink-light);
  }
  .brand__name {
    color: var(--ink-light);
    font-weight: 400;
    font-size: 20px;
    letter-spacing: 6px;
    padding-left: 6px;
  }
  .contact {
    position: absolute;
    left: 150px;
    top: 95px;
  }
  .contact__name {
    color: var(--ink-light);
    font-weight: 700;
    font-size: 11px;
    letter-spacing: 1.1px;
    text-transform: uppercase;
    margin-bottom: 8px;
  }
  .contact__line {
    color: var(--ink-silver);
    font-weight: 400;
    font-size: 10.5px;
    letter-spacing: 0.6px;
    line-height: 17.5px;
    text-transform: uppercase;
  }
</style>
</head>
<body>
<main class="canvas">
  <section class="card card--front" aria-label="Frente do cartão">
    <div class="brand">
      <span class="brand__mark" aria-hidden="true"></span>
      <span class="brand__name">RWT</span>
    </div>
  </section>
  <section class="card card--back" aria-label="Verso do cartão">
    <div class="contact">
      <p class="contact__name">Marcela Tavares Rocha</p>
      <p class="contact__line">www.RWTimoveis-exemplo.com.br</p>
      <p class="contact__line">+554187316042</p>
      <p class="contact__line">marcela@rwtimoveis-exemplo.com.br</p>
    </div>
  </section>
</main>
</body>
</html>
```